Card Design for my dog training business Brightpaw Obedience

Need a business card design for my dog training business with my new logo. Want the card to come off professional yet fun. Want it to be very eye catchy as well. I normally have these at vet clinics, pet stores, and groomers. so need it to look better than my competitors.
Target Market(s)
dog owners
Industry/Entity Type
Dog Training
Contact Information for Business Card
needs logo, my name and info
Font styles to use
Serif
Colors
0255a3
ffffff
ec1f27
000000
333333
fbfbfb
Requirements
Must have
- Brightpaw Obedience
- Felix Orland
- 415 903 2276
- info@brightpawobedience.example
- www.brightpawobedience.example

```html
<!DOCTYPE html>
<html lang="en">
<head>
<meta charset="utf-8">
<title>Brightpaw Obedience – Business Card</title>
<link rel="stylesheet" href="https://fonts.googleapis.com/css2?family=Marcellus&family=EB+Garamond:ital@1&family=Open+Sans:wght@400&display=swap">
<style>
  :root {
    --brand-blue: #0255a3;
    --brand-blue-deep: #024a8f;
    --brand-red: #ec1f27;
    --ink-black: #000000;
    --ink-charcoal: #333333;
    --paper: #fbfbfb;
    --paper-shade: #e9e9e9;
    --white: #ffffff;
    --backdrop: #d6d6d6;
  }
  * { margin: 0; padding: 0; box-sizing: border-box; }
  html, body {
    width: 1200px; height: 576px; overflow: hidden;
    background: var(--backdrop);
  }
  .canvas { position: relative; width: 1200px; height: 576px; }

  .card {
    position: absolute; top: 138px;
    width: 484px; height: 293px;
    border-radius: 12px; overflow: hidden;
  }

  /* Front side */
  .card--front {
    left: 82px;
    background: linear-gradient(180deg, var(--brand-blue) 0%, var(--brand-blue-deep) 100%);
  }
  .front__brand {
    position: absolute; left: 0; right: 0; top: 92px;
    display: flex; flex-direction: column; align-items: center; gap: 10px;
    color: var(--white);
    font-family: "Marcellus", serif;
  }
  .brand-dot {
    width: 34px; height: 34px; border-radius: 50%;
    background: var(--white);
  }
  .front__name { font-size: 26px; letter-spacing: 1px; }
  .front__band {
    position: absolute; left: 0; right: 0; top: 255px; height: 28px;
    background: var(--ink-black);
    display: flex; align-items: center; justify-content: center;
  }
  .tagline {
    font-family: "EB Garamond", serif; font-style: italic;
    font-size: 12.5px; white-space: nowrap;
  }
  .front__band .tagline { color: var(--white); }

  /* Back side */
  .card--back {
    left: 602px; width: 481px; height: 292px;
    background: linear-gradient(180deg, var(--white) 0%, var(--paper) 60%, var(--paper-shade) 100%);
  }
  .back__waves { position: absolute; inset: 0; }
  .back__person {
    position: absolute; right: 36px; top: 24px; text-align: right;
  }
  .person__name {
    font-family: "Marcellus", serif; font-size: 21px;
    color: var(--white);
  }
  .person__role {
    font-family: "Open Sans", sans-serif; font-size: 11px;
    color: #e2e2e2; margin-top: 2px;
  }
  .back__brand {
    position: absolute; left: 22px; top: 150px; width: 160px;
    display: flex; flex-direction: column; align-items: center; gap: 8px;
    font-family: "Marcellus", serif; color: var(--ink-charcoal);
    text-align: center;
  }
  .back__brand .brand-dot { background: var(--ink-charcoal); width: 28px; height: 28px; }
  .back__brand .brand-name { font-size: 19px; line-height: 1.15; }

  .contact-list {
    position: absolute; right: 30px; top: 186px;
    list-style: none;
    font-family: "Open Sans", sans-serif; font-size: 12px;
    color: var(--ink-charcoal);
  }
  .contact-list li {
    display: flex; align-items: center; justify-content: flex-end;
    gap: 10px; height: 19px;
  }
  .contact-icon { width: 12px; height: 12px; fill: var(--brand-blue); }
  .back__tagline {
    position: absolute; right: 30px; top: 250px;
    color: var(--ink-charcoal);
  }
</style>
</head>
<body>
<main class="canvas">

  <section class="card card--front" aria-label="Card front">
    <div class="front__brand">
      <span class="brand-dot" aria-hidden="true"></span>
      <span class="front__name">Brightpaw Obedience</span>
    </div>
    <div class="front__band">
      <p class="tagline">“Building good manners one happy pup at a time.”</p>
    </div>
  </section>

  <section class="card card--back" aria-label="Card back">
    <svg class="back__waves" viewBox="0 0 481 292" width="481" height="292" aria-hidden="true">
      <path fill="var(--ink-charcoal)" d="M0,0 H481 V106 C400,110 330,92 262,62 C195,34 100,22 0,40 Z"/>
      <path fill="var(--brand-red)" d="M0,58 C70,30 160,20 246,34 C160,28 70,40 0,72 Z"/>
      <path fill="var(--white)" d="M30,70 C120,40 200,38 262,62 C330,92 400,110 481,110 V114 C400,116 330,98 262,68 C200,46 120,46 30,70 Z"/>
      <path fill="var(--brand-blue)" d="M40,72 C120,46 200,44 262,68 C330,98 400,116 481,116 V125 C400,125 330,108 262,78 C200,54 120,52 40,72 Z"/>
    </svg>

    <div class="back__person">
      <p class="person__name">Felix Orland</p>
      <p class="person__role">Dog Trainer</p>
    </div>

    <div class="back__brand">
      <span class="brand-dot" aria-hidden="true"></span>
      <span class="brand-name">Brightpaw<br>Obedience</span>
    </div>

    <ul class="contact-list">
      <li>415 903 2276
        <svg class="contact-icon" viewBox="0 0 12 12" aria-hidden="true"><path d="M1,4 C1,2 3,1 6,1 C9,1 11,2 11,4 L9,5 L8,3.5 H4 L3,5 Z M3,6 H9 L10,11 H2 Z"/></svg>
      </li>
      <li>info@brightpawobedience.example
        <svg class="contact-icon" viewBox="0 0 12 12" aria-hidden="true"><path d="M1,3 H11 V10 H1 Z M1.8,3.6 L6,7 L10.2,3.6 V4.6 L6,8 L1.8,4.6 Z" fill-rule="evenodd"/></svg>
      </li>
      <li>www.brightpawobedience.example
        <svg class="contact-icon" viewBox="0 0 12 12" aria-hidden="true"><circle cx="6" cy="6" r="5"/><path d="M1,6 H11 M6,1 V11 M6,1 C3.5,3.5 3.5,8.5 6,11 M6,1 C8.5,3.5 8.5,8.5 6,11" stroke="var(--white)" stroke-width="0.7" fill="none"/></svg>
      </li>
    </ul>

    <p class="tagline back__tagline">“Building good manners one happy pup at a time.”</p>
  </section>

</main>
</body>
</html>
```